Meridian Tidewren Pale Ale Beer Label/Badge

We need a Beer Label designed for our first official beer to be launched under The meridian Brand!!
It will be a Pale Ale Called "Tidewren Pale Ale"!

The Meridian has the largest Craft Beer & Cider selection in the Geelong & Surf Coast region. With a funky location and a relaxed vibe, Meridian prides itself on serving delicious, unique seasonal food paired with Australia's best Craft Beer. The meridian is the perfect setting for a relaxed afternoon or evening with friends and can package an experience for larger groups or corporate bookings.

The Meridian Tavern brand has been growing for over a year and a half and the first label needs to integrate The meridian Logo but at the same time bring a fresh, new and eye catching feel to it along with embracing the "Odysseus" story in which we will be naming future beers.

The story of Tidewren is found via the following link
http://lorevault.example/wiki/Tidewren_(folklore)

We expect designers to research The meridian Tavern brand along with the all important Craft Beer Market and demographics. This will, potentially, be the start of many more labels to come for the winning designer!!

Requirements
Must have
• The original "O" needs to be integrated into the new logo and as much as the Greek mythology is being used it needs to be certain that this is an original Australian Craft Beer in the modern age!!
strong, modern & unique!!
Nice to have
• Logo could have a depiction of Tidewren
Should not have
• tackiness or cheap!!

```html
<!DOCTYPE html>
<html lang="en">
<head>
<meta charset="utf-8">
<title>Meridian Tidewren Pale Ale – Label</title>
<link rel="stylesheet" href="https://fonts.googleapis.com/css2?family=Russo+One&family=Caesar+Dressing&family=Josefin+Sans:wght@300;700&display=swap">
<style>
  :root {
    --page: #ffffff;
    --label-olive: #a69d77;
    --panel-sand: #cdc49c;
    --cream: #fbf6e3;
    --brick: #a4473b;
    --terracotta: #a85c4c;
    --artwork-light: #f3eee0;
    --artwork-mid: #e2dac2;
  }
  html, body {
    margin: 0;
    padding: 0;
    width: 747px;
    height: 1200px;
    overflow: hidden;
    background: var(--page);
  }
  .label {
    display: block;
    width: 747px;
    height: 1200px;
  }
  .label-ground { fill: var(--label-olive); }
  .panel { fill: var(--panel-sand); }
  .brand-name {
    font-family: "Russo One", sans-serif;
    font-size: 76px;
    fill: var(--cream);
  }
  .brand-tagline {
    font-family: "Josefin Sans", sans-serif;
    font-weight: 700;
    font-size: 27px;
    fill: var(--cream);
  }
  .brand-mark { fill: var(--brick); }
  .beer-name {
    font-family: "Caesar Dressing", fantasy;
    font-size: 92px;
    fill: var(--terracotta);
  }
  .beer-style {
    font-family: "Josefin Sans", sans-serif;
    font-weight: 300;
    font-size: 98px;
    fill: var(--cream);
  }
</style>
</head>
<body>
<svg class="label" viewBox="0 0 747 1200" xmlns="http://www.w3.org/2000/svg">
  <defs>
    <radialGradient id="artwork-tone" cx="50%" cy="45%" r="60%">
      <stop offset="0%" stop-color="var(--artwork-light)"/>
      <stop offset="100%" stop-color="var(--artwork-mid)"/>
    </radialGradient>
  </defs>

  <rect class="label-ground" x="96" y="128" width="550" height="918"/>

  <path class="panel panel-top" d="M122,140 Q122,128 134,128 H600 Q612,128 612,140 V290 L380,510 Q373,517 366,510 L122,290 Z"/>
  <path class="panel panel-bottom" d="M366,527 Q373,520 380,527 L612,745 V896 Q612,908 600,908 H134 Q122,908 122,896 V745 Z"/>

  <text class="brand-name" x="371" y="230" text-anchor="middle" textLength="416" lengthAdjust="spacingAndGlyphs">MERIDIAN</text>
  <text class="brand-tagline" x="368" y="271" text-anchor="middle" textLength="394" lengthAdjust="spacing">TAVERN + BREWERY</text>

  <circle class="brand-mark" cx="370" cy="370" r="70"/>

  <rect role="img" aria-label="Illustration of Tidewren in a crested helmet within a laurel wreath, set on a classical column capital"
        x="285" y="585" width="166" height="172" rx="10" fill="url(#artwork-tone)"/>

  <text class="beer-name" x="366" y="885" text-anchor="middle" textLength="428" lengthAdjust="spacingAndGlyphs">TIDEWREN</text>

  <text class="beer-style" x="366" y="1010" text-anchor="middle" textLength="412" lengthAdjust="spacingAndGlyphs">PALE ALE</text>
</svg>
</body>
</html>
```